Church Website with Home Page and Member Sermon Library

I am in need of an updated design for our church website. This will include 4 pages (outlined below). We are a conservative, evangelical, Christian church. The site should be modern and clean, while still reflecting our conservative values. I already have a logo for our church, and I want the site to incorporate the logo, and match the logo/branding. Stock photos are allowed if needed, but I have uploaded some images of our church and would prefer those images to be used if possible. Any stock photos used should not include any people in the photos (scenery, nature, buildings, animals, etc. are fine).

The site will need 4 pages: Home, Support Us (Donate), Login, and Recording Library.

Page 1: Home
The home page should include the following sections:

- Navigation: Should include links to each section of the home page plus a "listen live" link which will take the user to a live-streaming site and a "support us" link which will take the user to a support/donate page.

- Announcements: Can be either a banner or some other design, but there needs to be some way for us to post announcements for visitors to see. I'm open for creative ideas in this section, but would like it not to take up a lot of room on the page.

- About Us: Should include address, service times (see attached document), and information about the church.

- Pastor Bio: A section that introduces our pastor and gives a short bio about our pastor. Would like this section to include a picture of our pastor. Somewhere in this section I would like to include this Bible reference: "And I will give you pastors according to mine heart, which shall feed you with knowledge and understanding. Jer 3:15 LPW"

- Articles of Faith (What We Believe): This should include several sub-sections each with a heading, body, and possibly 1 or more scripture references. I have attached a document to the brief that includes our articles of faith. Feel free to be creative with this section in how you lay these out and format them.

- Support Us: A small section that explains what kind of support someone can give and a link to a donation page. The link can say something like "Support Us" or "Donate Now".

- Contact form: A contact form that allows the visitor to send us a message. The contact form should ask for name, email, phone, and message.

- Footer: A footer that will be displayed on all pages of the site. This should include at a minimum a link to the home page (or a link to each individual section in the home page if you prefer), a link to "listen live", a link to "support us", a link to "contact us" (or you can put the contact form directly in the footer if you prefer), the address, and a "member login" link.

Page 2: Support Us
The donation page should include a form the visitor can fill out to make a donation. We will embed a third party form later. For this design, please just mock out the design with a basic form asking for name, phone, and email.

Page 3: Login
The recording library (detailed below) will require members to login with a shared numeric code before accessing the page. We need a design for a login screen. The screen should include navigation/footer just like all other pages, but the body of the login page will consist only of a form that asks the user to enter the access code and then a "login" button.

Page 4: Recording Library

The library page is a member-only page that will require a shared, numeric pass code to access. On this page, members will be able to access a filterable list of past sermons. The page by default should display most recent sermons, but should also include a search form that allows the member to filter the sermon list to find a particular sermon. The search form should allow the user to select a filter type (e.g. Speaker name, date, event, etc.) and type in a value to search. They should be able to add multiple filters and remove filters that have been added. Each sermon that is displayed in the result list should include basic information such as title, date, speaker, tags, etc. along with a download icon, and an embedded audio player where they can click a play button to stream it on-demand. Each sermon should also have clickable tags associated with it that can be used to find related sermons.
Updates

I have uploaded several images of our church. Feel free to incorporate these into your design if possible.

Target Market(s)

Church Members

Industry/Entity Type

Religion

Number of Pages Required

4 page

Font styles to use
Sans Serif

Colors

Designer to choose colors to be used in the design.

Requirements
Must have
• Must incorporate the logo (attached)
Nice to have
• Would like the design to incorporate pictures of our church (attached) instead of stock photos if possible.
Should not have
• Please avoid an overly cluttered design. Stock photos used should not include any people in the photos.

```html
<!DOCTYPE html>
<html lang="en">
<head>
<meta charset="utf-8">
<title>Sermon Library – Cedar Grove Church</title>
<link href="https://fonts.googleapis.com/css2?family=Cinzel:wght@400;600&family=Montserrat:wght@400;500;600&display=swap" rel="stylesheet">
<style>
:root{
  --green:#7fa86c;
  --green-dark:#3f5e33;
  --ink:#1c1c1c;
  --muted:#8a8a8a;
  --line:#dcdcdc;
  --footer:#2c2c2c;
  --footer-text:#c9c9c9;
  --footer-head:#e2e2e2;
  --white:#ffffff;
}
*{box-sizing:border-box;margin:0;padding:0}
html,body{width:753px;height:1200px;overflow:hidden;background:var(--white)}
body{position:relative;font-family:"Montserrat",sans-serif;color:var(--ink)}
.abs{position:absolute}

/* hero */
.hero{left:0;top:0;width:753px;height:285px;
  background:linear-gradient(180deg,#fbf9f6 0%,#f3e7da 30%,#d9b48e 62%,#b98457 100%)}
.brand{left:80px;top:36px;width:110px;text-align:center;font-family:"Cinzel",serif;color:var(--green);font-size:15px;letter-spacing:1px;line-height:1.1}
.brand small{display:block;font-size:6px;letter-spacing:4px;color:#6c6c6c}
.brand .dot{display:block;width:18px;height:18px;border-radius:50%;background:#27b5c9;margin:0 auto 6px}
.nav{right:108px;top:21px;display:flex;gap:35px;font-size:10px}
.nav a{color:var(--ink);text-decoration:none}
.page-title{left:0;width:753px;top:150px;text-align:center;font-family:"Cinzel",serif;font-weight:400;font-size:35px;letter-spacing:3px;color:var(--ink)}
.rule{left:326px;top:199px;width:101px;height:2px;background:var(--ink)}
.rule.thin{left:352px;top:203px;width:49px;height:1px}

/* search */
.search{left:108px;top:262px;width:537px;height:40px;background:var(--white)}
.select{left:113px;top:268px;width:95px;height:33px;background:#f1f1f1;font-size:9.5px;color:#555;display:flex;align-items:center;padding-left:16px;gap:8px}
.field{left:208px;top:268px;width:349px;height:33px;border:1px solid var(--line);display:flex;align-items:center;padding-left:12px;gap:6px;font-size:8.5px;color:#aaa}
.btn{left:557px;top:268px;width:82px;height:33px;background:var(--green);color:var(--white);font-size:9.5px;font-weight:600;display:flex;align-items:center;justify-content:center}
.chip{top:319px;height:21px;border:1px solid var(--line);border-radius:11px;font-size:8.5px;letter-spacing:1px;color:#444;display:flex;align-items:center;padding:0 10px;gap:8px}

/* sermon cards */
.card{width:261px;height:162px;overflow:hidden;color:var(--white)}
.card .photo{position:absolute;inset:0;background:linear-gradient(160deg,#d7dcd2 0%,#9aa893 40%,#4f6b43 75%,#355029 100%)}
.card .shade{position:absolute;inset:0;background:linear-gradient(180deg,rgba(60,90,48,.55) 0%,rgba(60,90,48,0) 25%,rgba(60,90,48,.35) 55%,rgba(52,82,40,.95) 100%)}
.card .dl{position:absolute;left:12px;top:11px;font-size:7.5px;display:flex;gap:5px;align-items:center}
.card .date{position:absolute;left:12px;top:84px;font-size:7px;display:flex;gap:4px;align-items:center}
.card h3{position:absolute;left:12px;top:95px;font-family:"Cinzel",serif;font-weight:600;font-size:8.5px;letter-spacing:.8px}
.card .desc{position:absolute;left:12px;top:108px;width:170px;font-size:5.6px;line-height:1.25;opacity:.9}
.card .by{position:absolute;left:12px;top:129px;font-size:7.5px;display:flex;align-items:center;gap:5px}
.card .avatar{width:13px;height:13px;border-radius:50%;background:#c8b6a0}
.card .tags{position:absolute;left:12px;top:143px;font-size:7.5px;display:flex;align-items:center;gap:2px}
.card .tag{border:1px solid rgba(255,255,255,.8);border-radius:7px;padding:1px 5px;letter-spacing:.5px}
.card .play{position:absolute;left:203px;top:76px;width:44px;height:44px;border-radius:50%;background:rgba(255,255,255,.4);border:1.5px solid rgba(255,255,255,.7)}

/* player */
.player{width:261px;height:162px;overflow:hidden;box-shadow:0 2px 6px rgba(0,0,0,.2)}
.player .photo{position:absolute;left:0;top:0;width:261px;height:127px;background:linear-gradient(160deg,#f3f1ee 0%,#d9d2c8 45%,#7d7a78 80%,#34363d 100%)}
.player .bar{position:absolute;left:0;top:127px;width:261px;height:35px;background:#2f2f2f}
.player .time{position:absolute;top:115px;font-size:5.5px;color:var(--white)}
.player .track{position:absolute;left:0;top:126px;width:261px;height:1.5px;background:#999}
.player .done{position:absolute;left:0;top:126px;width:178px;height:1.5px;background:#3fc36d}
.player .knob{position:absolute;left:173px;top:121px;width:11px;height:11px;border-radius:50%;background:var(--white)}

/* pager */
.pager{left:335px;top:894px;display:flex;align-items:center;gap:10px;font-family:"Cinzel",serif;font-size:7px}
.pager .box{width:20px;height:20px;border:1px solid var(--line);display:flex;align-items:center;justify-content:center;color:var(--green)}

/* footer */
.footer{left:0;top:956px;width:753px;height:244px;background:var(--footer)}
.live{left:110px;top:1030px;width:140px;height:40px;border-radius:20px;background:#f2f0ec;border:2px solid var(--green);box-shadow:0 6px 12px rgba(0,0,0,.4);display:flex;align-items:center;gap:12px;padding-left:3px;font-family:"Cinzel",serif;font-weight:600;font-size:9px;color:var(--green)}
.live .disc{width:32px;height:32px;border-radius:50%;background:var(--green)}
.f-head{font-family:"Cinzel",serif;font-size:10px;letter-spacing:1px;color:var(--footer-head)}
.f-text{font-size:8.5px;line-height:1.25;color:var(--footer-text)}
.f-brand{left:300px;top:1076px;width:153px;text-align:center;font-family:"Cinzel",serif;font-size:20px;color:var(--green);letter-spacing:1px}
.f-brand small{display:block;font-size:8px;letter-spacing:6px;color:#506b45}
.f-links{left:517px;top:1043px;display:flex;flex-direction:column;gap:7px;font-size:8.5px;color:var(--footer-text)}
.f-rule{left:0;top:1154px;width:753px;height:1px;background:#3a3a3a}
.copyright{left:110px;top:1169px;font-size:7.5px;color:#dddddd}
.social{left:573px;top:1166px;display:flex;gap:10px}
.social span{width:7px;height:7px;border-radius:50%;background:#e6e6e6}
</style>
</head>
<body>

<div class="abs hero" role="img" aria-label="Wooden church pews in soft light"></div>
<div class="abs brand"><span class="dot"></span>Cedar Grove<small>Church</small></div>
<nav class="abs nav"><a href="#">About Us</a><a href="#">Articles Of Faith</a><a href="#">Contact Us</a></nav>
<h1 class="abs page-title">LIBRARY</h1>
<div class="abs rule"></div><div class="abs rule thin"></div>

<div class="abs search"></div>
<div class="abs select">SPEAKER <svg width="7" height="5" viewBox="0 0 7 5"><path d="M1 1l2.5 2.5L6 1" fill="none" stroke="#555" stroke-width="1.2"/></svg></div>
<div class="abs field"><svg width="9" height="9" viewBox="0 0 10 10"><circle cx="4" cy="4" r="3" fill="none" stroke="#aaa" stroke-width="1.2"/><path d="M6.3 6.3L9 9" stroke="#aaa" stroke-width="1.2"/></svg>Type your request here</div>
<div class="abs btn">ADD FILTER</div>
<div class="abs chip" style="left:113px">EVENT: Wedding <span>×</span></div>
<div class="abs chip" style="left:238px">SPEAKER: Elias Warren <span>×</span></div>

<!-- sermons -->
<div class="abs card" style="left:108px;top:358px">
  <div class="photo" role="img" aria-label="Pastor preaching from the pulpit"></div><div class="shade"></div>
  <div class="dl"><svg width="8" height="8" viewBox="0 0 8 8"><path d="M4 0v5M2 3l2 2 2-2M0 7h8" fill="none" stroke="#9fcf8a" stroke-width="1"/></svg>Download</div>
  <div class="date"><svg width="6" height="6" viewBox="0 0 6 6"><rect x=".5" y="1" width="5" height="4.5" fill="none" stroke="#fff" stroke-width=".8"/></svg>Fab 12, 2023</div>
  <h3>ULLAMCORPER FACILISI EGESTAS</h3>
  <p class="desc">Ut diam tortor consectetur lacus scelerisque tortor congue viverra egestas.</p>
  <div class="by"><span class="avatar"></span>by: Marian Holt</div>
  <div class="tags">search tags: <span class="tag">Ullamcorper facilis</span><span class="tag">facilis</span><span class="tag">Ullamcorper</span></div>
  <div class="play"><svg width="44" height="44" viewBox="0 0 44 44"><path d="M18 14l10 8-10 8z" fill="#fff"/></svg></div>
</div>

<div class="abs card" style="left:384px;top:358px">
  <div class="photo" role="img" aria-label="Minister reading beside a green plant"></div><div class="shade"></div>
  <div class="dl"><svg width="8" height="8" viewBox="0 0 8 8"><path d="M4 0v5M2 3l2 2 2-2M0 7h8" fill="none" stroke="#9fcf8a" stroke-width="1"/></svg>Download</div>
  <div class="date"><svg width="6" height="6" viewBox="0 0 6 6"><rect x=".5" y="1" width="5" height="4.5" fill="none" stroke="#fff" stroke-width=".8"/></svg>Fab 12, 2023</div>
  <h3>ULLAMCORPER FACILISI EGESTAS</h3>
  <p class="desc">Ut diam tortor consectetur lacus scelerisque tortor congue viverra egestas.</p>
  <div class="by"><span class="avatar"></span>by: Marian Holt</div>
  <div class="tags">search tags: <span class="tag">Ullamcorper facilis</span><span class="tag">facilis</span><span class="tag">Ullamcorper</span></div>
  <div class="play"><svg width="44" height="44" viewBox="0 0 44 44"><path d="M18 14l10 8-10 8z" fill="#fff"/></svg></div>
</div>

<div class="abs card" style="left:108px;top:535px">
  <div class="photo" role="img" aria-label="Minister reading beside a green plant"></div><div class="shade"></div>
  <div class="dl"><svg width="8" height="8" viewBox="0 0 8 8"><path d="M4 0v5M2 3l2 2 2-2M0 7h8" fill="none" stroke="#9fcf8a" stroke-width="1"/></svg>Download</div>
  <div class="date"><svg width="6" height="6" viewBox="0 0 6 6"><rect x=".5" y="1" width="5" height="4.5" fill="none" stroke="#fff" stroke-width=".8"/></svg>Fab 12, 2023</div>
  <h3>ULLAMCORPER FACILISI EGESTAS</h3>
  <p class="desc">Ut diam tortor consectetur lacus scelerisque tortor congue viverra egestas.</p>
  <div class="by"><span class="avatar"></span>by: Marian Holt</div>
  <div class="tags">search tags: <span class="tag">Ullamcorper facilis</span><span class="tag">facilis</span><span class="tag">Ullamcorper</span></div>
  <div class="play"><svg width="44" height="44" viewBox="0 0 44 44"><path d="M18 14l10 8-10 8z" fill="#fff"/></svg></div>
</div>

<div class="abs player" style="left:384px;top:535px">
  <div class="photo" role="img" aria-label="Pastor preaching, now playing"></div>
  <div class="bar"></div>
  <span class="time" style="left:6px">23:25</span><span class="time" style="right:7px">20:41</span>
  <div class="track"></div><div class="done"></div><div class="knob"></div>
  <svg class="abs" style="left:100px;top:138px" width="60" height="12" viewBox="0 0 60 12">
    <rect x="0" y="2" width="1.5" height="8" fill="#fff"/><path d="M9 2L2.5 6 9 10z" fill="#fff"/>
    <rect x="25" y="2" width="1.5" height="8" fill="#fff"/><rect x="29" y="2" width="1.5" height="8" fill="#fff"/>
    <path d="M51 2l6.5 4L51 10z" fill="#fff"/><rect x="58" y="2" width="1.5" height="8" fill="#fff"/>
  </svg>
  <svg class="abs" style="left:241px;top:139px" width="10" height="9" viewBox="0 0 10 9"><path d="M0 3h2l3-3v9L2 6H0z" fill="#ccc"/><path d="M7 2.5a3 3 0 010 4M8.5 1a5 5 0 010 7" fill="none" stroke="#ccc" stroke-width=".8"/></svg>
</div>

<div class="abs card" style="left:108px;top:711px">
  <div class="photo" role="img" aria-label="Pastor preaching from the pulpit"></div><div class="shade"></div>
  <div class="dl"><svg width="8" height="8" viewBox="0 0 8 8"><path d="M4 0v5M2 3l2 2 2-2M0 7h8" fill="none" stroke="#9fcf8a" stroke-width="1"/></svg>Download</div>
  <div class="date"><svg width="6" height="6" viewBox="0 0 6 6"><rect x=".5" y="1" width="5" height="4.5" fill="none" stroke="#fff" stroke-width=".8"/></svg>Fab 12, 2023</div>
  <h3>ULLAMCORPER FACILISI EGESTAS</h3>
  <p class="desc">Ut diam tortor consectetur lacus scelerisque tortor congue viverra egestas.</p>
  <div class="by"><span class="avatar"></span>by: Marian Holt</div>
  <div class="tags">search tags: <span class="tag">Ullamcorper facilis</span><span class="tag">facilis</span><span class="tag">Ullamcorper</span></div>
  <div class="play"><svg width="44" height="44" viewBox="0 0 44 44"><path d="M18 14l10 8-10 8z" fill="#fff"/></svg></div>
</div>

<div class="abs card" style="left:384px;top:711px">
  <div class="photo" role="img" aria-label="Minister reading beside a green plant"></div><div class="shade"></div>
  <div class="dl"><svg width="8" height="8" viewBox="0 0 8 8"><path d="M4 0v5M2 3l2 2 2-2M0 7h8" fill="none" stroke="#9fcf8a" stroke-width="1"/></svg>Download</div>
  <div class="date"><svg width="6" height="6" viewBox="0 0 6 6"><rect x=".5" y="1" width="5" height="4.5" fill="none" stroke="#fff" stroke-width=".8"/></svg>Fab 12, 2023</div>
  <h3>ULLAMCORPER FACILISI EGESTAS</h3>
  <p class="desc">Ut diam tortor consectetur lacus scelerisque tortor congue viverra egestas.</p>
  <div class="by"><span class="avatar"></span>by: Marian Holt</div>
  <div class="tags">search tags: <span class="tag">Ullamcorper facilis</span><span class="tag">facilis</span><span class="tag">Ullamcorper</span></div>
  <div class="play"><svg width="44" height="44" viewBox="0 0 44 44"><path d="M18 14l10 8-10 8z" fill="#fff"/></svg></div>
</div>

<div class="abs pager">
  <svg width="6" height="10" viewBox="0 0 6 10"><path d="M5 1L1 5l4 4" fill="none" stroke="#ccc" stroke-width="1.2"/></svg>
  <span class="box">1</span><span>of <b>16</b></span>
  <svg width="6" height="10" viewBox="0 0 6 10"><path d="M1 1l4 4-4 4" fill="none" stroke="#7fa86c" stroke-width="1.4"/></svg>
</div>

<!-- footer -->
<footer class="abs footer"></footer>
<div class="abs live"><span class="disc"></span>LISTEN LIVE</div>
<div class="abs f-head" style="left:116px;top:1091px">LOCATION</div>
<div class="abs f-text" style="left:116px;top:1109px;display:flex;gap:5px">
  <svg width="7" height="9" viewBox="0 0 7 9"><path d="M3.5 8.5S.5 5.5.5 3.5a3 3 0 016 0c0 2-3 5-3 5z" fill="none" stroke="#7fa86c" stroke-width=".9"/></svg>
  <span>418 Orchard Lane, Millbrook,<br>Ohio 43210</span>
</div>
<div class="abs f-brand">Cedar Grove<small>Church</small></div>
<div class="abs f-head" style="left:517px;top:1023px">QUICK LINKS</div>
<div class="abs f-links"><span>About Us</span><span>Articles Of Faith</span><span>Support Our Ministry</span><span>Contact Us</span><span>Member Login</span></div>
<div class="abs f-rule"></div>
<div class="abs copyright">Copyright 2023 Cedar Grove Church I All rights reserved</div>
<div class="abs social"><span></span><span></span><span></span><span></span></div>

</body>
</html>
```